Inspirational Quotes Poster Set

Brookloft is a stylish coworking space, which has a design-oriented vintage look from the 60's with an industrial touch (www.brookloft-example.com) Brookloft Quote Poster Set of 16 posters. The poster should be typo oriented and rather simple. Reflecting a bit the clean billboard design from the sixties. Minimal / simple graphical elements

Target Market(s)

Startups and Entrepreneurs

Industry/Entity Type

Startup

Font styles to use
Sans Serif

Colors

Designer to choose colors to be used in the design.

Requirements
Must have
• Posters need to be on and very stylish

```html
<!DOCTYPE html>
<html lang="en">
<head>
<meta charset="utf-8">
<title>Brookloft Quote Poster Set</title>
<link rel="stylesheet" href="https://fonts.googleapis.com/css2?family=Archivo:wdth,wght@100..125,700..800&display=swap">
<style>
  :root {
    --track-red: #ad361b;
    --track-red-light: #b9452a;
    --chalk-white: #ffffff;
    --hive-yellow: #fbc52d;
  }
  html, body {
    margin: 0;
    padding: 0;
    overflow: hidden;
    background: var(--track-red);
  }
  .poster {
    position: relative;
    width: 801px;
    height: 1200px;
    overflow: hidden;
    background: var(--track-red);
    font-family: "Archivo", "Helvetica Neue", Arial, sans-serif;
    font-stretch: 118%;
    color: var(--chalk-white);
  }
  .track-artwork {
    position: absolute;
    inset: 0;
    background: radial-gradient(ellipse 75% 55% at 62% 45%, var(--track-red-light) 0%, var(--track-red) 100%);
  }
  .quote {
    position: absolute;
    left: 70px;
    top: 322px;
    margin: 0;
    font-size: 88px;
    line-height: 79.3px;
    font-weight: 800;
    letter-spacing: -0.04em;
  }
  .attribution {
    position: absolute;
    left: 71px;
    top: 1010px;
    margin: 0;
    font-size: 25px;
    line-height: 28px;
    font-weight: 700;
    letter-spacing: -0.045em;
  }
  .brand {
    position: absolute;
    left: 70px;
    top: 1094px;
    display: flex;
    align-items: center;
    gap: 10px;
  }
  .brand-name {
    margin: 0;
    font-size: 50px;
    line-height: 54px;
    font-weight: 800;
    letter-spacing: -0.045em;
  }
  .brand-mark {
    width: 14px;
    height: 14px;
    margin-top: 14px;
    background: var(--hive-yellow);
  }
</style>
</head>
<body>
  <main class="poster">
    <div class="track-artwork" role="img" aria-label="Running track lanes with white lines curving in an arch around the quote"></div>

    <h1 class="quote">chase the<br>vision,<br>not the<br>money;<br>the money<br>will end up<br>following<br>you</h1>

    <p class="attribution">Theo Marsden,<br>CEO of Solecraft</p>

    <div class="brand">
      <p class="brand-name">brookloft</p>
      <span class="brand-mark" aria-hidden="true"></span>
    </div>
  </main>
</body>
</html>
```